Business Card Design for Flood Rescue 360 - Property Restoration Professionals

I need a business card designed for Flood Rescue 360. We are a full-service property restoration solution. Providing water, fire, smoke & storm restoration as well as mold remediation and full remodel or reconstruction to homes and businesses across Dallas-Fort Worth, TX.
Target Market(s)
home and business owners with insurance covered property damage from water, fire or storm related damage
Industry/Entity Type
property restoration
Contact Information for Business Card
Marcus Pelley General Manager Cell: 214-555-0193 Office: 469-555-0148 email: Marcus@FloodRescue360.example services: Water, Fire, Mold, Reconstruction Tagline: Fast Help When Flood Waters Rise!
Look and feel
Each slider illustrates characteristics of the customer's brand and the style your logo design should communicate.

```html
<!DOCTYPE html>
<html lang="en">
<head>
<meta charset="utf-8">
<title>Flood Rescue 360 – Business Card</title>
<link rel="stylesheet" href="https://fonts.googleapis.com/css2?family=Montserrat:wght@400;600;700;800&display=swap">
<style>
  :root {
    --page-bg: #d9d4cd;
    --card-top: #2a2a2a;
    --card-bottom: #151515;
    --teal: #1a9aa5;
    --text-warm: #cfc2ad;
    --text-grey: #c4c0ba;
  }
  * { margin: 0; padding: 0; box-sizing: border-box; }
  html, body { width: 1200px; height: 1047px; overflow: hidden; }
  body {
    background: var(--page-bg);
    font-family: "Montserrat", sans-serif;
    position: relative;
  }
  .business-card {
    position: absolute;
    left: 100px; top: 250px;
    width: 1000px; height: 547px;
    border-radius: 24px;
    background: linear-gradient(160deg, var(--card-top), var(--card-bottom));
    box-shadow: 0 20px 50px rgba(0,0,0,.25);
    overflow: hidden;
  }
  .brand {
    position: absolute;
    right: 38px; top: 36px;
    display: flex; align-items: center; gap: 22px;
  }
  .brand-name {
    font-weight: 800;
    color: var(--teal);
    font-size: 62px;
    line-height: 0.98;
    text-align: right;
    letter-spacing: -0.5px;
  }
  .brand-mark {
    width: 130px; height: 130px;
    border-radius: 50%;
    border: 8px solid var(--teal);
  }
  .accent-bar {
    position: absolute; left: 4px; top: 192px;
    width: 16px; height: 79px;
    background: var(--teal);
  }
  .person-name {
    position: absolute; left: 41px; top: 192px;
    font-size: 42px; font-weight: 600; color: var(--teal);
  }
  .person-title {
    position: absolute; left: 41px; top: 245px;
    font-size: 24px; font-weight: 400; color: var(--text-warm);
  }
  .tagline {
    position: absolute; left: 44px; top: 306px;
    font-size: 25px; font-weight: 400; color: var(--text-warm);
  }
  .contact-list {
    position: absolute; left: 44px; top: 362px;
    list-style: none;
  }
  .contact-list li {
    display: flex; align-items: center; gap: 12px;
    height: 38.5px;
    font-size: 26px; color: var(--text-grey);
  }
  .contact-list svg { width: 20px; height: 20px; fill: var(--teal); flex: none; }
  .services {
    position: absolute; right: 38px; top: 308px;
    text-align: right;
  }
  .services-heading {
    font-size: 39px; font-weight: 700; color: var(--teal);
    margin-bottom: 16px;
  }
  .services-list { list-style: none; }
  .services-list li {
    display: flex; justify-content: flex-end; align-items: center; gap: 9px;
    height: 38px;
    font-size: 25px; color: var(--text-warm);
  }
  .service-dot {
    width: 14px; height: 14px; border-radius: 50%;
    border: 2.5px solid var(--teal); flex: none; margin-top: 6px;
  }
</style>
</head>
<body>
  <main class="business-card">
    <div class="brand">
      <div class="brand-name">FLOOD<br>RESCUE 360</div>
      <div class="brand-mark" aria-hidden="true"></div>
    </div>

    <div class="accent-bar"></div>
    <h1 class="person-name">Marcus Pelley</h1>
    <p class="person-title">General Manager</p>

    <p class="tagline">Fast Help When Flood Waters Rise!</p>

    <ul class="contact-list">
      <li>
        <svg viewBox="0 0 20 20" aria-hidden="true"><path d="M6 1h8a1.5 1.5 0 0 1 1.5 1.5v15A1.5 1.5 0 0 1 14 19H6a1.5 1.5 0 0 1-1.5-1.5v-15A1.5 1.5 0 0 1 6 1zm0 2v12h8V3zm4 13a1 1 0 1 0 0 2 1 1 0 0 0 0-2z"/></svg>
        214-555-0193
      </li>
      <li>
        <svg viewBox="0 0 20 20" aria-hidden="true"><path d="M1 7c2-3 16-3 18 0l-1 2-4-1V6H6v2L2 9zm4 2h10l3 8H2zm5 2a2.5 2.5 0 1 0 0 5 2.5 2.5 0 0 0 0-5z"/></svg>
        469-555-0148
      </li>
      <li>
        <svg viewBox="0 0 20 20" aria-hidden="true"><path d="M1 5h18v11H1zm2 2v.4l7 4.6 7-4.6V7zm0 2.8V14h14V9.8l-7 4.6z"/></svg>
        Marcus@FloodRescue360.example
      </li>
      <li>
        <svg viewBox="0 0 20 20" aria-hidden="true"><path d="M10 1a9 9 0 1 0 0 18 9 9 0 0 0 0-18zm-1 3 1 2-2 2 1 2-3 1-2-3 1-3zm5 1 3 3-1 4-2 2-2-2 1-3-1-2z"/></svg>
        FloodRescue360.example
      </li>
    </ul>

    <section class="services">
      <h2 class="services-heading">SERVICES</h2>
      <ul class="services-list">
        <li>Water <span class="service-dot"></span></li>
        <li>Fire <span class="service-dot"></span></li>
        <li>Mold <span class="service-dot"></span></li>
        <li>Reconstruction <span class="service-dot"></span></li>
      </ul>
    </section>
  </main>
</body>
</html>
```